design a construction company business card

Design business card around our logo. Card must have all the typical info: name, title, address, phone, email, business name, etc. Somewhere on the card I would like to see our motto "Built on integrity... Inspired by commitment." Consider adding a splash of bright orange to the card to complement the blues and silvers/grays in the logo. We are open to metallic inks, textures, etc. We would like to see options on both light and dark backgrounds. The font in the logo is Euro Technic Extended Regular.

```html
<!DOCTYPE html>
<html lang="en">
<head>
<meta charset="utf-8">
<title>Halden Contracting – Business Card</title>
<link rel="stylesheet" href="https://fonts.googleapis.com/css2?family=Ubuntu:wght@400;500&family=Ubuntu+Condensed&display=swap">
<style>
  :root {
    --sheet: #ffffff;
    --frame: #222222;
    --orange: #ff6600;
    --black: #000000;
    --blue: #3a6fc4;
    --white: #ffffff;
  }
  * { box-sizing: border-box; margin: 0; padding: 0; }
  html, body { width: 1200px; height: 1200px; overflow: hidden; background: var(--sheet); }
  .sheet {
    position: relative; width: 1200px; height: 1200px;
    border: 1.5px solid var(--frame); background: var(--sheet);
    font-family: "Ubuntu", sans-serif;
  }
  .card {
    position: absolute; left: 222px; width: 756px; height: 462px;
    background: var(--black); overflow: hidden;
  }
  .card--front { top: 120px; }
  .card--back { top: 618px; }
  .card__band { position: absolute; left: 0; top: 0; width: 100%; background: var(--orange); }
  .card--front .card__band { height: 238px; }
  .card--back .card__band { height: 130px; }

  .wordmark {
    position: absolute; left: 0; width: 100%; text-align: center;
    color: var(--blue); font-weight: 500; line-height: 1; white-space: nowrap;
  }
  .wordmark span { display: block; }
  .card--front .wordmark { top: 244px; }
  .card--front .wordmark__main { font-size: 100px; letter-spacing: 8px; }
  .card--front .wordmark__sub { font-size: 32px; letter-spacing: 6px; margin-top: 12px; }
  .card--back .wordmark { top: 134px; }
  .card--back .wordmark__main { font-size: 54px; letter-spacing: 5px; }
  .card--back .wordmark__sub { font-size: 16px; letter-spacing: 4px; margin-top: 6px; }

  .motto {
    position: absolute; top: 104px; font-family: "Ubuntu Condensed", sans-serif;
    font-size: 19px; letter-spacing: 1px; color: var(--black); white-space: nowrap;
  }
  .motto--left { left: 70px; }
  .motto--right { right: 12px; }

  .person { position: absolute; left: 0; top: 220px; width: 100%; text-align: center; }
  .person__name { color: var(--orange); font-size: 40px; font-weight: 500; letter-spacing: 1px; line-height: 1; }
  .person__title { color: var(--white); font-size: 17px; margin-top: 10px; }

  .contact {
    position: absolute; top: 354px; color: var(--white);
    font-size: 18px; line-height: 22px; white-space: nowrap;
  }
  .contact--phone { left: 40px; }
  .contact--address { right: 42px; text-align: right; font-style: normal; }
</style>
</head>
<body>
<div class="sheet">
  <section class="card card--front">
    <div class="card__band"></div>
    <div class="wordmark">
      <span class="wordmark__main">HALDEN</span>
      <span class="wordmark__sub">CONTRACTING, INC.</span>
    </div>
  </section>

  <section class="card card--back">
    <div class="card__band"></div>
    <p class="motto motto--left">Built On Integrity</p>
    <p class="motto motto--right">Inspired By Commitment</p>
    <div class="wordmark">
      <span class="wordmark__main">HALDEN</span>
      <span class="wordmark__sub">CONTRACTING, INC.</span>
    </div>
    <div class="person">
      <h1 class="person__name">Dana Whitlow</h1>
      <p class="person__title">Senior Project Manager</p>
    </div>
    <div class="contact contact--phone">
      <p>Phone: 555.201.4478</p>
      <p>Fax: 555.201.4479</p>
      <p>Email: info@haldencontracting.com</p>
    </div>
    <address class="contact contact--address">
      <p>Halden Contracting, Inc.</p>
      <p>2740 Larkfield Avenue</p>
      <p>Brookdale, OH 45010</p>
    </address>
  </section>
</div>
</body>
</html>
```